Haulage company, lets use ruby red white and some 3rd color for web design. and Garvel Pryce Transport logo

Target Market(s)

Transport industry

Industry/Entity Type

transport

Number of Pages Required

2 page

Requirements
Must have
• Logo

```html
<!DOCTYPE html>
<html lang="en">
<head>
<meta charset="utf-8">
<title>Garvel Pryce Transport</title>
<link href="https://fonts.googleapis.com/css2?family=Lexend:wght@300;400;500;600;700&display=swap" rel="stylesheet">
<style>
:root{
  --ruby:#9b0f1f;
  --ruby-soft:#b42a3a;
  --ruby-deep:#7e0b18;
  --white:#ffffff;
  --ink:#1d1d1d;
}
*{box-sizing:border-box;margin:0;padding:0}
html,body{width:1200px;height:3398px;overflow:hidden;background:var(--white)}
body{position:relative;font-family:"Lexend",sans-serif;font-weight:300;color:var(--ink)}
.abs{position:absolute}
.head{font-family:"Lexend",sans-serif;font-weight:600;text-transform:uppercase;letter-spacing:.5px}

/* hero + services */
.top-bg{left:0;top:0;width:1200px;height:1200px;
  background:linear-gradient(180deg,#b34856 0%,#a8303f 20%,#9b1524 45%,#a42233 60%,#b33a49 80%,#8f1423 100%)}
.brand{left:83px;top:62px;display:flex;align-items:center;gap:14px;color:var(--white);font-weight:600;font-size:22px;text-transform:uppercase;letter-spacing:.5px}
.brand-dot{width:30px;height:30px;border-radius:50%;border:3px solid var(--white)}
.nav{top:69px;color:var(--white);font-size:15px;font-weight:500}
.nav span{position:absolute;white-space:nowrap}
.welcome{left:0;width:1200px;top:290px;text-align:center;color:var(--white);font-size:31px;font-weight:700}
.btn-contact{left:520px;top:371px;width:158px;height:50px;border-radius:25px;background:var(--white);color:var(--ruby);font-weight:500;font-size:17px;display:flex;align-items:center;justify-content:center}
.services-title{left:0;width:1200px;top:686px;text-align:center;color:var(--white);font-size:38px;font-weight:700}
.services-text{left:180px;width:840px;top:755px;text-align:center;color:var(--white);font-size:15px;line-height:37px}
.service-label{top:963px;width:320px;text-align:center;color:var(--white);font-size:20px;font-weight:400}

/* about */
.about-red{left:638px;top:1200px;width:562px;height:683px;background:var(--ruby)}
.about-title{left:111px;top:1304px;color:var(--ruby);font-size:38px;font-weight:700}
.about-text{left:111px;top:1381px;width:392px;font-size:15px;line-height:35.2px}
.about-photo{left:537px;top:1296px;width:663px;height:494px;background:linear-gradient(180deg,#c9d2dc 0%,#dfe4ea 40%,#b8bcb0 62%,#cfd0cb 100%)}
.learn-circle{left:110px;top:1696px;width:72px;height:72px;border-radius:50%;border:2px solid var(--ruby)}
.learn-text{left:212px;top:1722px;color:var(--ruby);font-size:16px;font-weight:400}

/* news */
.news{left:0;top:1883px;width:1200px;height:725px;background:var(--ruby)}
.news-title{left:111px;top:1975px;color:var(--white);font-size:38px;font-weight:700}
.arrow-btn{top:1977px;width:44px;height:44px;border-radius:50%;border:2px solid var(--white)}
.card{top:2089px;width:311px;height:431px;background:var(--white)}
.card-img{height:188px;width:100%}
.card-date{position:absolute;left:22px;top:225px;color:var(--ruby);font-weight:500;font-size:18px}
.card-title{position:absolute;left:22px;top:265px;color:var(--ruby);font-weight:500;font-size:18px}
.card-text{position:absolute;left:22px;top:302px;width:280px;font-size:15px;line-height:35px}

/* subscribe */
.sub-title{left:109px;top:2686px;color:var(--ruby);font-weight:600;font-size:32px;line-height:56px}
.sub-text{left:110px;top:2804px;width:480px;font-size:15px;line-height:35px}
.sub-form{left:646px;top:2747px;width:442px;height:71px;border-radius:36px;background:var(--ruby)}
.sub-input{left:26px;top:24px;color:var(--white);font-size:16px;font-weight:400}
.sub-btn{left:268px;top:4px;width:170px;height:63px;border-radius:32px;background:var(--white);color:var(--ruby);font-weight:600;font-size:21px;display:flex;align-items:center;justify-content:center}

/* footer */
.rule{left:111px;width:978px;height:1px;background:#9a9a9a}
.vrule{top:2958px;width:1px;height:319px;background:#9a9a9a}
.f-head{top:2999px;color:var(--ruby);font-size:21px;font-weight:400}
.f-link{font-size:15px;font-weight:400;color:var(--ink)}
.f-brand{left:489px;width:290px;top:3060px;text-align:center;color:var(--ruby);font-weight:600;font-size:23px;line-height:42px;text-transform:uppercase}
.f-dot{left:617px;top:2995px;width:34px;height:34px;border-radius:50%;border:3px solid var(--ruby)}
.social{top:3169px;width:31px;height:31px;border-radius:50%;border:1.5px solid var(--ruby)}
.copy{left:0;width:1200px;top:3347px;text-align:center;font-size:16px;font-weight:400}
.copy .accent{color:var(--ruby)}
</style>
</head>
<body>

<div class="abs top-bg" role="img" aria-label="Red-tinted photograph of two lorries on a coastal road above an airliner on a runway"></div>

<div class="abs brand"><span class="brand-dot"></span>Garvel Pryce Transport</div>
<nav class="abs nav" style="left:0;width:1200px">
  <span style="left:637px">HOME</span>
  <span style="left:729px">ABOUT US</span>
  <span style="left:853px">OUR SERVICES</span>
  <span style="left:1013px">CONTACT US</span>
</nav>

<svg class="abs" style="left:0;top:0" width="1200" height="1200" fill="none" stroke="#fff" stroke-width="1.3">
  <path d="M111 123V257M111 343V541H580M622 541H1088V343M1088 257V123M601 562V679"/>
  <circle cx="112" cy="301" r="21"/><path d="M116 292l-8 9 8 9"/>
  <circle cx="1089" cy="301" r="21" fill="#fff"/><path d="M1085 292l8 9-8 9" stroke="#9b0f1f" stroke-width="2"/>
  <rect x="587" y="520" width="28" height="42" rx="14"/><path d="M601 528v14M595 537l6 6 6-6"/>
  <g stroke-width="2">
    <rect x="222" y="868" width="60" height="38" rx="3"/><path d="M222 918h66M230 906v8M274 906v8M240 868v-10h30v10M252 880h28l-6 16h-18z"/>
    <rect x="573" y="880" width="50" height="30" rx="2"/><path d="M623 888h12l7 10v12h-19M566 890h10M562 898h12M566 906h10"/>
    <circle cx="587" cy="914" r="5"/><circle cx="632" cy="914" r="5"/><circle cx="604" cy="870" r="9"/><circle cx="598" cy="895" r="6"/>
    <circle cx="928" cy="872" r="9"/><circle cx="974" cy="914" r="9"/><path d="M928 881c0 8 0 12 12 12h30c10 0 10 12 0 12h-40c-10 0-10 12 0 12h30"/>
  </g>
</svg>

<div class="abs head welcome">Welcome to Garvel Pryce Transport</div>
<div class="abs btn-contact">CONTACT US</div>

<div class="abs head services-title">Our Services</div>
<p class="abs services-text">Lorem ipsum dolor sit amet, consectetur adipiscing elit, sed do eiusmod tempor incididunt ut labore et<br>dolore magna aliqua. Ut enim ad minim veniam.</p>
<div class="abs service-label" style="left:93px">LOREM IPSUM DOLOR</div>
<div class="abs service-label" style="left:441px">LOREM IPSUM DOLOR</div>
<div class="abs service-label" style="left:791px;top:972px">LOREM IPSUM DOLOR</div>

<div class="abs about-red"></div>
<h2 class="abs head about-title">About Us</h2>
<p class="abs about-text">Lorem ipsum dolor sit amet, consectetur<br>adipiscing elit, sed do eiusmod tempor incididunt<br>ut labore et dolore magna aliqua. Ut enim ad<br>minim veniam, quis nostrud exercitation ullamco<br>laboris nisi ut aliquip ex ea commodo consequat.<br>Duis aute irure dolor in reprehenderit in voluptate<br>velit esse cillum dolore eu fugiat nulla pariatur.<br>Excepteur sint occaecat.</p>
<div class="abs about-photo" role="img" aria-label="Photograph of two white and maroon lorry cabs parked on a concrete yard"></div>
<div class="abs learn-circle"></div>
<svg class="abs" style="left:134px;top:1720px" width="24" height="24" fill="none" stroke="#9b0f1f" stroke-width="2.5"><path d="M3 12h17M13 5l7 7-7 7"/></svg>
<div class="abs learn-text">LEARN MORE ABOUT US</div>

<section class="abs news"></section>
<h2 class="abs head news-title">Latest News</h2>
<div class="abs arrow-btn" style="left:967px"></div>
<div class="abs arrow-btn" style="left:1043px"></div>
<svg class="abs" style="left:0;top:1977px" width="1200" height="44" fill="none" stroke="#fff" stroke-width="2"><path d="M992 15l-7 7 7 7M1062 15l7 7-7 7"/></svg>

<article class="abs card" style="left:111px">
  <div class="card-img" role="img" aria-label="Photograph of a lorry on an open road at sunset" style="background:linear-gradient(180deg,#3d4a5a 0%,#d08a3a 45%,#4b5a30 75%,#3a3a3a 100%)"></div>
  <div class="card-date">06TH APRIL 2024</div>
  <div class="card-title">LOREM IPSUM DOLOR SIT</div>
  <p class="card-text">Lorem ipsum dolor sit amet,<br>consectetur adipiscing elit, sed do<br>eiusmod tempor.</p>
</article>
<article class="abs card" style="left:444px">
  <div class="card-img" role="img" aria-label="Photograph of a cargo port with containers, lorries and a plane at sunset" style="background:linear-gradient(180deg,#6a7a90 0%,#e4a04a 40%,#8a4a2a 70%,#3a3a44 100%)"></div>
  <div class="card-date">06TH MAY 2024</div>
  <div class="card-title">LOREM IPSUM DOLOR SIT</div>
  <p class="card-text">Lorem ipsum dolor sit amet,<br>consectetur adipiscing elit, sed do<br>eiusmod tempor.</p>
</article>
<article class="abs card" style="left:778px">
  <div class="card-img" role="img" aria-label="Photograph of traffic on a motorway with a lorry at dusk" style="background:linear-gradient(180deg,#d2a46a 0%,#e8c48a 35%,#8a8a78 65%,#5a5a5e 100%)"></div>
  <div class="card-date">06TH JUNE 2024</div>
  <div class="card-title">LOREM IPSUM DOLOR SIT</div>
  <p class="card-text">Lorem ipsum dolor sit amet,<br>consectetur adipiscing elit, sed do<br>eiusmod tempor.</p>
</article>

<h2 class="abs sub-title">SUBSCRIBE TO OUR<br>NEWSLETTER</h2>
<p class="abs sub-text">Lorem ipsum dolor sit amet, consectetur adipiscing elit, sed<br>do eiusmod tempor.</p>
<div class="abs sub-form">
  <span class="abs sub-input">ENTER EMAIL ADDRESS</span>
  <span class="abs sub-btn">SUBSCRIBE</span>
</div>

<div class="abs rule" style="top:2920px"></div>
<div class="abs vrule" style="left:489px"></div>
<div class="abs vrule" style="left:779px"></div>

<div class="abs f-head" style="left:111px">QUICK LINKS</div>
<div class="abs f-link" style="left:111px;top:3061px">HOME</div>
<div class="abs f-link" style="left:111px;top:3103px">ABOUT US</div>
<div class="abs f-link" style="left:111px;top:3146px">OUR SERVICES</div>
<div class="abs f-link" style="left:111px;top:3189px">TESTIMONIALS</div>

<div class="abs f-head" style="left:311px">HELP</div>
<div class="abs f-link" style="left:311px;top:3061px">PRIVACY POLICY</div>
<div class="abs f-link" style="left:311px;top:3103px">TERMS OF USE</div>
<div class="abs f-link" style="left:311px;top:3146px">CONTACT</div>

<div class="abs f-dot"></div>
<div class="abs f-brand">Garvel Pryce<br>Transport</div>
<div class="abs social" style="left:541px"></div>
<div class="abs social" style="left:578px"></div>
<div class="abs social" style="left:615px"></div>
<div class="abs social" style="left:652px"></div>
<div class="abs social" style="left:689px"></div>

<div class="abs f-head" style="left:845px">GET IN TOUCH</div>
<svg class="abs" style="left:845px;top:3058px" width="24" height="120" fill="#9b0f1f">
  <path d="M4 2l5 0 2 5-3 2c1 3 3 5 6 6l2-3 5 2v5c-10 0-17-7-17-17z"/>
  <path d="M1 46h21v14H1z M1 46l10.5 8L22 46" stroke="#fff" stroke-width="1.5"/>
  <path d="M11 86c-5 0-8 4-8 8 0 6 8 14 8 14s8-8 8-14c0-4-3-8-8-8z"/><circle cx="11" cy="94" r="3" fill="#fff"/>
</svg>
<div class="abs f-link" style="left:886px;top:3061px">+1 555 014 2290</div>
<div class="abs f-link" style="left:886px;top:3103px">HELLO@GARVELPRYCE.COM</div>
<div class="abs f-link" style="left:886px;top:3146px;line-height:43px;width:200px">52, GARVEL PRYCE<br>TRANSPORT LOREM<br>418 276</div>

<div class="abs rule" style="top:3317px"></div>
<div class="abs copy">@2024 COPYRIGHTS &nbsp;&nbsp;&nbsp;&nbsp;|&nbsp;&nbsp;&nbsp;&nbsp; <span class="accent">GARVEL PRYCE TRANSPORT</span> &nbsp;&nbsp;&nbsp;&nbsp;|&nbsp;&nbsp;&nbsp;&nbsp; ALL RIGHTS RESERVED</div>

</body>
</html>
```